Stationery Design Project

I need a stationary design for our company. we are based in Houston, TX and we are called Mira Vell Lending. And we are wanting to brand our MoneyMendPlus program, which includes our tax preparation and restoration, credit repair service. Although our business offers other programs, we are interested in mainly focusing on The MoneyMendPlus program. We are looking for way to brand our ourselves and I believe that a great stationery design will help in achieving this goal. Our logo design is blue and light blue. the slogan is orange.

Industry/Entity Type

Business

Requirements
Must have
• Address: 30871 Calloway Ln. B-22
Houston, TX 75419
Tel. 555-318-6207
Fax 555-294-7153
www.miravelllending.example
info@miravelllending.example
Our Slogan: Happiness, Restored!

```html
<!DOCTYPE html>
<html lang="en">
<head>
<meta charset="utf-8">
<title>MoneyMendPlus Business Card Set</title>
<link rel="stylesheet" href="https://fonts.googleapis.com/css2?family=Marcellus+SC&family=Source+Sans+3:wght@400;600&family=Libre+Baskerville&display=swap">
<style>
  :root {
    --backdrop: #e7e2da;
    --card-white: #ffffff;
    --navy: #103f68;
    --navy-deep: #0d3558;
    --sky: #1e93d2;
    --orange: #f29a1e;
    --orange-light: #fbc02d;
    --ink: #333333;
    --frame-light: #d6e8f5;
  }
  * { box-sizing: border-box; margin: 0; padding: 0; }
  html, body { width: 1200px; height: 800px; overflow: hidden; }
  body { background: var(--backdrop); font-family: "Source Sans 3", Arial, sans-serif; }
  .stage { position: relative; width: 1200px; height: 800px; }

  .card {
    position: absolute; width: 509px; height: 290px; border-radius: 22px;
    box-shadow: 0 6px 14px rgba(0,0,0,.25); overflow: hidden;
  }
  .card--front { left: 78px; top: 90px; background: var(--card-white); }
  .card--back-white { left: 621px; top: 90px; background: var(--card-white); }
  .card--back-navy { left: 75px; top: 450px; background: var(--navy); }
  .card--back-framed { left: 621px; top: 450px; background: var(--navy); }

  /* front */
  .program-name {
    position: absolute; left: 0; right: 0; top: 100px; text-align: center;
    font-family: "Source Sans 3", Arial, sans-serif; font-weight: 600;
    font-size: 46px; color: var(--navy); letter-spacing: -0.5px;
  }
  .contact-band { position: absolute; left: 0; top: 182px; width: 509px; height: 66px; }
  .contact-phone {
    position: absolute; left: 44px; top: 198px; font-size: 14px; line-height: 17px; color: var(--ink);
  }
  .contact-phone b { font-style: italic; font-weight: 600; }
  .contact-web {
    position: absolute; right: 46px; top: 198px; text-align: right;
    font-size: 14px; line-height: 17px; color: #ffffff;
  }
  .address {
    position: absolute; left: 0; right: 0; top: 256px; text-align: center;
    font-size: 14px; color: var(--ink);
  }

  /* backs */
  .slogan {
    position: absolute; left: 0; right: 0; top: 22px; text-align: center;
    font-family: "Marcellus SC", Georgia, serif; font-size: 20px; letter-spacing: 1px; color: var(--orange);
  }
  .website {
    position: absolute; left: 0; right: 0; top: 242px; text-align: center;
    font-size: 21px; letter-spacing: 2px; color: var(--ink);
  }
  .card--back-navy .website, .card--back-framed .website { color: #ffffff; top: 250px; }
  .card--back-navy .slogan, .card--back-framed .slogan { top: 20px; }

  .brand-box {
    position: absolute; left: 169px; top: 60px; width: 171px; height: 170px;
    border: 1px solid var(--navy); padding: 5px;
  }
  .brand-box__fill {
    width: 100%; height: 100%; background: var(--navy);
    display: flex; align-items: flex-end; justify-content: center; padding-bottom: 26px;
  }
  .brand-frame {
    position: absolute; left: 170px; top: 55px; width: 169px; height: 169px;
    border: 4px solid var(--frame-light);
    display: flex; align-items: flex-end; justify-content: center; padding-bottom: 26px;
  }
  .company-name {
    font-family: "Libre Baskerville", Georgia, serif; color: #ffffff; font-size: 13px; white-space: nowrap;
  }
  .company-name--large {
    position: absolute; left: 0; right: 0; top: 202px; text-align: center; font-size: 19px;
  }
</style>
</head>
<body>
<main class="stage">

  <section class="card card--front" aria-label="Card front">
    <div class="program-name">MoneyMendPlus</div>
    <svg class="contact-band" viewBox="0 0 509 66" aria-hidden="true">
      <defs>
        <linearGradient id="bandOrange" x1="0" x2="1">
          <stop offset="0" stop-color="#f28a1a"/><stop offset="1" stop-color="#fbbf2a"/>
        </linearGradient>
        <linearGradient id="bandBlue" x1="0" x2="1">
          <stop offset="0" stop-color="#103f68"/><stop offset="1" stop-color="#1e93d2"/>
        </linearGradient>
      </defs>
      <polygon points="0,0 242,0 180,66 0,66" fill="url(#bandOrange)"/>
      <polygon points="236,0 509,0 509,66 178,66" fill="#ffffff"/>
      <polygon points="244,0 509,0 509,66 186,66" fill="url(#bandBlue)"/>
    </svg>
    <div class="contact-phone">
      <div><b>p</b> : 555-318-6207</div>
      <div><b>f</b> : 555-294-7153</div>
    </div>
    <div class="contact-web">
      <div>e : info@miravelllending.example</div>
      <div>w : www.miravelllending.example</div>
    </div>
    <div class="address">30871 Calloway Ln. B-22, Houston, TX 75419</div>
  </section>

  <section class="card card--back-white" aria-label="Card back, white">
    <div class="slogan">Happiness, Restored!</div>
    <div class="brand-box">
      <div class="brand-box__fill"><span class="company-name">Mira Vell Lending</span></div>
    </div>
    <div class="website">www.miravelllending.example</div>
  </section>

  <section class="card card--back-navy" aria-label="Card back, navy">
    <div class="slogan">Happiness, Restored!</div>
    <div class="company-name company-name--large">Mira Vell Lending</div>
    <div class="website">www.miravelllending.example</div>
  </section>

  <section class="card card--back-framed" aria-label="Card back, framed">
    <div class="slogan">Happiness, Restored!</div>
    <div class="brand-frame"><span class="company-name">Mira Vell Lending</span></div>
    <div class="website">www.miravelllending.example</div>
  </section>

</main>
</body>
</html>
```